Brimsett Gardening Fresh New Website

We are looking to create a simple fresh website for our landscaping business. The website should appeal to a 'high end' audience. We deal with a lot of Embassies and affluent clients who have extremely large gardens that are meticulously maintained. The site is about communicating our excellent landscaping and customer service skills and encouraging new clients to reach out and engage us to take care of their gardens.

The website is basically going to be our business card, it will have almost no functionality other than two 'contact us' forms, one for smaller clients and one for more detailed projects.

The website will not have a lot of written content and will have to show photos of beautifully landscaped gardens.

The main logo in black will influence the site, however, we are open to all suggestions.

We are expecting to have the following pages:
Home Page
Services
About Us
Contact Us
Showcase (photo gallery of our work)

We need someone who can code it to wordpress and be available for minor changes over a number of days. They will be simple tweaks.

```html
<!DOCTYPE html>
<html lang="en">
<head>
<meta charset="UTF-8">
<title>Brimsett Gardening</title>
<link href="https://fonts.googleapis.com/css2?family=Libre+Baskerville:wght@400;700&family=Roboto:wght@400;500&display=swap" rel="stylesheet">
<style>
:root{
  --ink:#111111;
  --white:#ffffff;
  --gold:#b8862b;
  --gold-light:#f3d34a;
  --gold-grad:linear-gradient(90deg,#b8862b,#f3d34a);
  --text:#1d1d1d;
  --grass-dark:#2f4a1c;
  --grass:#5f8a2e;
}
*{box-sizing:border-box;margin:0;padding:0}
html,body{width:1200px;height:3107px;overflow:hidden}
body{position:relative;background:var(--white);font-family:'Roboto',sans-serif;color:var(--text)}
.abs{position:absolute}
.serif{font-family:'Libre Baskerville',serif;font-weight:700}
.gold{color:var(--gold)}
.btn{position:absolute;background:var(--gold-grad);color:var(--ink);font-weight:500;font-size:13px;display:flex;align-items:center;justify-content:center}

/* header */
.site-header{left:0;top:0;width:1200px;height:92px;background:var(--ink);color:var(--white)}
.social{display:flex;gap:10px}
.social span{width:13px;height:13px;border:1.5px solid #ddd;border-radius:50%;display:block}
.header-phone{right:142px;top:16px;font-size:13px;display:flex;align-items:center;gap:8px}
.nav-line{top:45px;height:1px;background:#444}
.nav-link{top:59px;font-size:13px}
.brand{left:500px;top:34px;width:154px;text-align:center;font-family:'Libre Baskerville',serif;font-size:12px;letter-spacing:3px;color:var(--gold);line-height:1.5}

/* hero */
.hero{left:0;top:92px;width:1200px;height:563px;background:linear-gradient(180deg,#6f7a4a 0%,#3f5a25 45%,#5e8a2f 75%,#7aa23e 100%);border-bottom:2px solid #8a8a8a}
.hero-kicker{left:0;top:291px;width:1200px;text-align:center;color:var(--white);font-size:24px;letter-spacing:3px;font-weight:500}
.hero-title{left:0;top:330px;width:1200px;text-align:center;color:var(--white);font-size:46px}

/* quote form */
.quote{left:693px;top:609px;width:372px;height:441px;background:var(--ink);border:5px solid var(--gold)}
.quote h3{position:absolute;left:24px;top:24px;font-size:20px;line-height:1.35;color:var(--white)}
.field{position:absolute;left:24px;width:315px;height:35px;border:1px solid #cfcfcf;color:var(--white);font-size:12.5px;padding:0 14px;display:flex;align-items:center;justify-content:space-between}
.field b{color:#e23;font-weight:400}
.field.msg{height:70px;align-items:flex-start;padding-top:11px}

/* about */
.about-title{left:141px;top:708px;font-size:36px;line-height:1.3}
.about-text{left:141px;top:808px;width:450px;font-size:12.5px;line-height:22.5px}
.about-text p+p{margin-top:6px}

/* services */
.services-band{left:0;top:1138px;width:1200px;height:336px;background:linear-gradient(180deg,#4d4d46 0%,#3c4330 50%,#2d4a1f 100%)}
.section-title{left:0;width:1200px;text-align:center;font-size:36px}
.service-photo{width:271px;height:271px;border-radius:50%}
.service-arc{width:281px;height:281px}
.service-name{width:300px;text-align:center;font-size:17px;top:1578px}

/* reviews */
.review-box{left:282px;top:1752px;width:635px;height:163px;border:1.5px solid var(--gold);border-top-left-radius:40px;background:var(--white)}
.review-box p{position:absolute;left:50px;top:46px;width:535px;text-align:center;font-size:12.5px;line-height:22.5px}
.review-author{left:282px;top:1870px;width:635px;text-align:center;font-size:13.5px;font-weight:500}

/* cta */
.cta{left:0;top:2025px;width:1200px;height:430px;background:linear-gradient(135deg,#27391a 0%,#3f5d24 45%,#2e4520 100%)}
.cta-title{left:0;top:2160px;width:1200px;text-align:center;color:var(--white);font-size:36px}
.cta-text{left:220px;top:2216px;width:760px;text-align:center;color:#eee;font-size:12.5px;line-height:22.5px}

/* gallery */
.dark-band{left:0;top:2725px;width:1200px;height:345px;background:var(--ink)}
.gallery-item{top:2613px;width:175px;height:172px}

/* footer */
.footer-brand{left:141px;top:2930px;width:150px;text-align:center;font-family:'Libre Baskerville',serif;font-size:16px;letter-spacing:5px;line-height:1.6;color:var(--gold)}
.footer-mark{left:196px;top:2882px;width:40px;height:40px;border:2px solid var(--gold);border-radius:50%}
.footer-link{top:2888px;color:var(--white);font-size:12.5px}
.footer-line{left:404px;top:2930px;width:654px;height:1px;background:#444}
.contact-item{top:2959px;display:flex;align-items:center;gap:13px;color:var(--white);font-size:12.5px;line-height:15px}
.contact-icon{width:36px;height:36px;border-radius:50%;background:var(--gold-grad);display:flex;align-items:center;justify-content:center}
.bottom-bar{left:0;top:3070px;width:1200px;height:37px;background:var(--gold-grad);font-size:12px;color:var(--ink)}
.bottom-bar .copy{position:absolute;left:141px;top:12px}
.bottom-bar .social{position:absolute;right:142px;top:12px;gap:14px}
.bottom-bar .social span{border-color:var(--ink)}
</style>
</head>
<body>

<header class="abs site-header">
  <div class="abs social" style="left:141px;top:18px" aria-label="Social links"><span></span><span></span><span></span></div>
  <div class="abs header-phone">
    <svg width="14" height="14" viewBox="0 0 24 24" fill="none" stroke="#fff" stroke-width="1.8"><path d="M5 3h4l2 5-2.5 1.5a11 11 0 0 0 6 6L16 13l5 2v4a2 2 0 0 1-2 2A17 17 0 0 1 3 5a2 2 0 0 1 2-2z"/></svg>
    123 456 7890
  </div>
  <div class="abs nav-line" style="left:141px;width:293px"></div>
  <div class="abs nav-line" style="left:711px;width:347px"></div>
  <a class="abs nav-link" style="left:141px">Home</a>
  <a class="abs nav-link" style="left:246px">Services</a>
  <a class="abs nav-link" style="left:366px">Gallery</a>
  <div class="abs brand">BRIMSETT<br>GARDENING</div>
  <a class="abs nav-link" style="left:714px">About Us</a>
  <a class="abs nav-link" style="left:838px">Contact Us</a>
  <a class="abs nav-link" style="left:971px;display:flex;gap:6px;align-items:center">Projects For
    <svg width="12" height="8" viewBox="0 0 12 8" fill="none" stroke="#fff" stroke-width="1.6"><path d="M1 1l5 5 5-5"/></svg></a>
</header>

<section class="abs hero" role="img" aria-label="Manicured lawn and hedges beside a modern building at sunset"></section>
<div class="abs hero-kicker">LANDSCAPE PROS</div>
<h1 class="abs hero-title serif">Elegance In Every Landscape</h1>
<a class="btn" style="left:534px;top:406px;width:132px;height:35px">Request A Quote</a>

<form class="abs quote">
  <h3 class="serif"><span class="gold">24% Off</span> <span style="color:#c9c9c9">For New</span><br>Landscape Services</h3>
  <div class="field" style="top:84px"><span>Name<b>*</b></span></div>
  <div class="field" style="top:126px"><span>Email<b>*</b></span></div>
  <div class="field" style="top:168px"><span>Phone Number<b>*</b></span></div>
  <div class="field" style="top:210px"><span>Street Address &amp; Zip Code<b>*</b></span></div>
  <div class="field" style="top:252px"><span>Which Service Would You Like A Bill For?</span>
    <svg width="13" height="8" viewBox="0 0 12 8" fill="none" stroke="#fff" stroke-width="1.6"><path d="M1 1l5 5 5-5"/></svg></div>
  <div class="field msg" style="top:294px"><span>Message</span></div>
  <div class="btn" style="left:24px;top:373px;width:315px;height:35px">Request A Quote</div>
</form>

<h2 class="abs about-title serif">About<br><span class="gold">Brimsett Gardening</span></h2>
<div class="abs about-text">
  <p>Lorem Ipsum Is Simply Dummy Text Of The Printing And Typesetting Industry. Lorem Ipsum Has Been The Industry's Standard Dummy Text Ever Since The 1500s, When An Unknown Printer Took A Galley Of Type And Scrambled It To Make A Type Specimen Book.</p>
  <p>Lorem Ipsum Is Simply Dummy Text Of The Printing And Typesetting Industry. Lorem Ipsum Has Been The Industry's Standard Dummy Text Ever Since The 1500s, When&nbsp; And Scrambled It To Make A Type Specimen Book.</p>
</div>
<a class="btn" style="left:141px;top:988px;width:94px;height:35px">Read More</a>

<section class="abs services-band" role="img" aria-label="Office courtyard with flowerbeds and hedges"></section>
<h2 class="abs section-title serif" style="top:1212px;color:var(--white)">Our <span class="gold">Services</span></h2>

<div class="abs service-photo" style="left:144px;top:1286px;background:radial-gradient(circle at 50% 35%,#9cc063,#4f8a22 70%)" role="img" aria-label="Lawn with flowering shrubs"></div>
<svg class="abs service-arc" style="left:139px;top:1281px" viewBox="0 0 281 281"><path d="M3 160 A138 138 0 0 0 278 160" fill="none" stroke="#f3d34a" stroke-width="6"/></svg>
<div class="abs service-photo" style="left:464px;top:1286px;background:radial-gradient(circle at 50% 50%,#c9c7bf,#7c8a60 70%)" role="img" aria-label="Aerial view of a paved patio with gazebo"></div>
<svg class="abs service-arc" style="left:459px;top:1281px" viewBox="0 0 281 281"><path d="M3 160 A138 138 0 0 0 278 160" fill="none" stroke="#a77a2a" stroke-width="6"/></svg>
<div class="abs service-photo" style="left:786px;top:1286px;background:radial-gradient(circle at 40% 50%,#7a9a58,#3c5a2a 75%)" role="img" aria-label="Gloved hand spraying plants"></div>
<svg class="abs service-arc" style="left:781px;top:1281px" viewBox="0 0 281 281"><path d="M3 160 A138 138 0 0 0 278 160" fill="none" stroke="#f3d34a" stroke-width="6"/></svg>

<div class="abs service-name serif" style="left:129px">Lawn Fertilizing</div>
<div class="abs service-name serif gold" style="left:449px">Patios</div>
<div class="abs service-name serif" style="left:771px">Weed Control</div>

<h2 class="abs section-title serif" style="top:1676px">Customer <span class="gold">Reviews</span></h2>
<div class="abs review-box"><p>Lorem Ipsum Is Simply Dummy Text Of The Printing And Typesetting Industry. Lorem Ipsum Has Been The Industry's Standard Dummy Text Ever Since The 1500s, When An Unknown Printer Took A Galley Of Type And Scrambled It To Make A Type Specimen Book.</p></div>
<svg class="abs" style="left:579px;top:1913px" width="42" height="26" viewBox="0 0 42 26"><path d="M0 2 L21 24 L42 2" fill="#fff" stroke="#b8862b" stroke-width="1.5"/><rect x="2" y="0" width="38" height="2" fill="#fff"/></svg>
<div class="abs review-author">– Dorian. K</div>
<svg class="abs" style="left:228px;top:1834px" width="26" height="26" viewBox="0 0 26 26" fill="none" stroke="#111" stroke-width="1.6"><circle cx="13" cy="13" r="12"/><path d="M15 8l-5 5 5 5"/></svg>
<svg class="abs" style="left:945px;top:1834px" width="26" height="26" viewBox="0 0 26 26" fill="none" stroke="#111" stroke-width="1.6"><circle cx="13" cy="13" r="12"/><path d="M11 8l5 5-5 5"/></svg>

<section class="abs cta" role="img" aria-label="Aerial view of a winding garden path with a lawn mower"></section>
<h2 class="abs cta-title serif">Build Your Outdoor Dream With Us</h2>
<p class="abs cta-text">Lorem Ipsum Is Simply Dummy Text Of The Printing And Typesetting Industry. Lorem Ipsum Has Been The Industry's Standard Dummy Text Ever Since The 1500s, When An Unknown Printer Took A Galley Of Type And Scrambled It To Make A Type Specimen Book.</p>
<a class="btn" style="left:551px;top:2279px;width:98px;height:34px">Contact Us</a>

<div class="abs dark-band"></div>
<h2 class="abs section-title serif" style="top:2534px">Work <span class="gold">Gallery</span></h2>
<div class="abs gallery-item" style="left:141px;background:linear-gradient(180deg,#4f6a3a,#8fb84a)" role="img" aria-label="Golf course fairway lined with pines"></div>
<div class="abs gallery-item" style="left:327px;background:linear-gradient(160deg,#a9c880,#4f8a30)" role="img" aria-label="Hand holding grass blades"></div>
<div class="abs gallery-item" style="left:513px;background:linear-gradient(180deg,#6f8a3a,#8a8a6a 55%,#6a8a30)" role="img" aria-label="Hay bale on a lawn"></div>
<div class="abs gallery-item" style="left:698px;background:linear-gradient(180deg,#9fc070,#4e7a2a 60%,#a0604a)" role="img" aria-label="Brick path through a park"></div>
<div class="abs gallery-item" style="left:884px;background:linear-gradient(180deg,#6a8a40,#8a7a66)" role="img" aria-label="Gardener unrolling turf"></div>

<div class="abs footer-mark"></div>
<div class="abs footer-brand">BRIMSETT<br>GARDENING</div>
<a class="abs footer-link" style="left:404px">Home</a>
<a class="abs footer-link" style="left:509px">Services</a>
<a class="abs footer-link" style="left:629px">Gallery</a>
<a class="abs footer-link" style="left:739px">About Us</a>
<a class="abs footer-link" style="left:862px">Project Me</a>
<a class="abs footer-link" style="left:994px">Contact Us</a>
<div class="abs footer-line"></div>

<div class="abs contact-item" style="left:401px">
  <span class="contact-icon"><svg width="16" height="16" viewBox="0 0 24 24" fill="none" stroke="#111" stroke-width="1.8"><path d="M12 22s7-7 7-12a7 7 0 0 0-14 0c0 5 7 12 7 12z"/><circle cx="12" cy="10" r="2.5"/></svg></span>
  <span>123, Street Name, City<br>Name, Country Name,&nbsp; 1234</span>
</div>
<div class="abs contact-item" style="left:659px">
  <span class="contact-icon"><svg width="15" height="15" viewBox="0 0 24 24" fill="none" stroke="#111" stroke-width="1.8"><path d="M5 3h4l2 5-2.5 1.5a11 11 0 0 0 6 6L16 13l5 2v4a2 2 0 0 1-2 2A17 17 0 0 1 3 5a2 2 0 0 1 2-2z"/></svg></span>
  <span>123 456 7890</span>
</div>
<div class="abs contact-item" style="left:842px">
  <span class="contact-icon"><svg width="15" height="15" viewBox="0 0 24 24" fill="none" stroke="#111" stroke-width="1.8"><rect x="3" y="5" width="18" height="14"/><path d="M3 6l9 7 9-7"/></svg></span>
  <span>Brimsettgardening@Mail.Com</span>
</div>

<footer class="abs bottom-bar">
  <span class="copy">© 2024 Brimsett Gardening. All Rights Reserved.</span>
  <div class="social" aria-label="Social links"><span></span><span></span><span></span></div>
</footer>

</body>
</html>
```